Business Card Design

We are a commercial real estate brokerage in San Francisco, leasing office buildings downtown.
I would like a clean, elegant look. Simple but powerful .

Industry/Entity Type

Business

Contact Information for Business Card

Derek Holloway
lic# 07258143
415.555.0172
derek@velt-commercial.example
velt-commercial.example

```html
<!DOCTYPE html>
<html lang="en">
<head>
<meta charset="utf-8">
<title>VELT Commercial – Business Card</title>
<link rel="stylesheet" href="https://fonts.googleapis.com/css2?family=Source+Sans+3:ital,wght@0,400;0,600;1,400&display=swap">
<style>
  :root {
    --backdrop: #9a9a9a;
    --card: #ebebed;
    --band: #637391;
    --rule: #4a4f58;
    --brand: #637391;
    --ink: #3f3f44;
    --on-band: #f2f3f6;
    --on-band-soft: #dfe3ea;
  }
  * { box-sizing: border-box; margin: 0; padding: 0; }
  html, body {
    width: 1105px; height: 1200px; overflow: hidden;
    background: var(--backdrop);
    font-family: "Source Sans 3", "Myriad Pro", sans-serif;
  }
  .canvas { position: relative; width: 1105px; height: 1200px; }
  .card {
    position: absolute; left: 182px; width: 746px; height: 427px;
    background: var(--card);
  }
  .card--front { top: 119px; }
  .card--back { top: 635px; }

  .brand-name {
    position: absolute; left: 0; right: 0;
    text-align: center; color: var(--brand);
    font-weight: 600; letter-spacing: 2px; line-height: 1;
  }
  .card--front .brand-name { top: 118px; font-size: 52px; }
  .card--back .brand-name { top: 170px; font-size: 58px; }

  .front-rule {
    position: absolute; left: 0; right: 0; top: 266px;
    height: 2px; background: var(--rule);
  }
  .contact-band {
    position: absolute; left: 0; right: 0; top: 271px; bottom: 0;
    background: var(--band);
  }
  .holder {
    position: absolute; right: 432px; top: 40px; text-align: right;
  }
  .holder__name { color: var(--on-band); font-size: 27px; font-weight: 600; line-height: 1.2; }
  .holder__licence { color: var(--on-band-soft); font-size: 20px; line-height: 1.4; }
  .contact-list {
    position: absolute; left: 343px; top: 20px; list-style: none;
  }
  .contact-list li {
    display: flex; align-items: center; gap: 9px;
    color: var(--on-band); font-size: 20px; line-height: 29px;
  }
  .contact-list svg { width: 17px; height: 17px; fill: var(--on-band); flex: none; }

  .tagline {
    position: absolute; left: 0; right: 0; top: 318px;
    text-align: center; color: var(--ink);
    font-style: italic; font-size: 19px; line-height: 27px;
  }
</style>
</head>
<body>
<main class="canvas">
  <section class="card card--front" aria-label="Card front">
    <p class="brand-name">VELT COMMERCIAL</p>
    <div class="front-rule"></div>
    <div class="contact-band">
      <div class="holder">
        <p class="holder__name">Derek Holloway</p>
        <p class="holder__licence">lic# 07258143</p>
      </div>
      <ul class="contact-list">
        <li>
          <svg viewBox="0 0 24 24" aria-hidden="true"><path d="M6.6 10.8a15.1 15.1 0 0 0 6.6 6.6l2.2-2.2c.3-.3.7-.4 1-.2 1.1.4 2.3.6 3.6.6.6 0 1 .4 1 1V20c0 .6-.4 1-1 1C10.6 21 3 13.4 3 4c0-.6.4-1 1-1h3.5c.6 0 1 .4 1 1 0 1.3.2 2.5.6 3.6.1.3 0 .7-.2 1z"/></svg>
          415.555.0172
        </li>
        <li>
          <svg viewBox="0 0 24 24" aria-hidden="true"><path d="M2 5h20v14H2z M3.5 6.5 12 13l8.5-6.5" fill="none" stroke="#f2f3f6" stroke-width="0"/><path d="M2 5h20v2l-10 7L2 7z"/><path d="M2 9l10 7 10-7v10H2z"/></svg>
          derek@velt-commercial.example
        </li>
        <li>
          <svg viewBox="0 0 24 24" aria-hidden="true"><circle cx="12" cy="12" r="10"/><path d="M8 7c2 1 3 0 4 2s-1 3 1 4 0 4 2 5M16 6c-1 2 1 3 2 3" fill="none" stroke="#637391" stroke-width="1.6"/></svg>
          velt-commercial.example
        </li>
      </ul>
    </div>
  </section>

  <section class="card card--back" aria-label="Card back">
    <p class="brand-name">VELT COMMERCIAL</p>
    <p class="tagline">commercial real estate brokerage in San Francisco<br>leasing office buildings downtown.</p>
  </section>
</main>
</body>
</html>
```